Redesign kavrin.ch agency website for unique design with speed and conversion

We want to redesign our website kavrin.ch. Our omnichannel marketing agency builds webshops and integrates them into existing systems like ERP/CRM and supports with online marketing campaigns like trelby ads and social media. The target of the redesign is to get a great look and feel for customers to see directly what we do, (please design something for our three focus areas eCommerce, Online marketing and Integration)
and to improve the pages speed drastically for SEO. Please see our attachment.
B2B
eCommerce Agency
Coded - Design and coding required
5+ page

```html
<!DOCTYPE html>
<html lang="en">
<head>
<meta charset="utf-8">
<title>kavrin.ch – Online Marketing Agency</title>
<link href="https://fonts.googleapis.com/css2?family=Righteous&family=Quicksand:wght@400;500;600;700&display=swap" rel="stylesheet">
<style>
:root{
  --green:#45e14a;
  --green-soft:#a2f89f;
  --ink:#141414;
  --muted:#3a3a3a;
  --mist:#eef3ee;
  --mist-2:#e6eae6;
  --white:#ffffff;
  --orange:#f47c14;
  --black:#050505;
}
*{box-sizing:border-box;margin:0;padding:0}
html,body{width:1200px;height:4862px;overflow:hidden}
body{position:relative;background:var(--white);font-family:"Quicksand",sans-serif;color:var(--ink)}
.abs{position:absolute}
.display{font-family:"Righteous",sans-serif;font-weight:400}
.section-title{position:absolute;left:0;width:1200px;text-align:center;font-family:"Righteous",sans-serif;font-size:30px;color:var(--ink)}
.section-title::after{content:"";display:block;width:62px;height:3px;background:var(--green);margin:12px auto 0;border-radius:2px}
.btn{display:inline-block;border-radius:20px;font-family:"Righteous",sans-serif;font-size:17px;padding:6px 26px;text-decoration:none}
.btn-fill{background:var(--green);color:var(--white)}
.btn-line{border:2px solid var(--ink);color:var(--ink);background:transparent}
.btn-ghost{border:2px solid var(--white);color:var(--white)}
.placeholder{border-radius:14px}

/* header */
.logo{font-family:"Righteous",sans-serif;color:var(--green);letter-spacing:4px}
.topbar{left:530px;top:20px;display:flex;gap:34px;font-size:14px;align-items:center}
.topbar span{display:flex;align-items:center;gap:14px}
.ico{width:28px;height:28px;border-radius:50%;background:var(--green);display:inline-flex;align-items:center;justify-content:center}
.nav-line{left:378px;top:62px;width:712px;height:1px;background:#d8d8d8}
.nav{left:382px;top:80px;display:flex;gap:34px;font-size:14px;font-weight:500}
.contact-btn{left:993px;top:68px;background:var(--green);color:var(--white);font-size:12px;font-weight:700;border-radius:16px;padding:8px 18px}

/* hero */
.hero{left:0;top:130px;width:1200px;height:520px;background:var(--green-soft);border-bottom-right-radius:260px}
.hero h1{position:absolute;left:100px;top:148px;font-family:"Righteous",sans-serif;font-size:38px;line-height:1.22;width:470px;font-weight:400}
.hero p{position:absolute;left:102px;top:300px;font-size:16px;width:340px;line-height:1.45;font-weight:500}
.hero .actions{position:absolute;left:100px;top:370px;display:flex;gap:16px}

/* cards */
.card{position:absolute;top:772px;width:485px;height:260px;background:var(--white);border-radius:12px;box-shadow:0 4px 16px rgba(0,0,0,.12)}
.card .badge{position:absolute;left:14px;top:14px;width:66px;height:66px;border-radius:14px;display:flex;align-items:center;justify-content:center}
.card h3{position:absolute;left:92px;top:24px;font-family:"Righteous",sans-serif;font-size:24px;line-height:1.35;font-weight:400;width:370px}
.card p{position:absolute;left:92px;top:100px;width:370px;font-size:13px;line-height:1.75;height:92px;overflow:hidden}
.card a{position:absolute;left:92px;top:206px;font-family:"Righteous",sans-serif;font-size:15px;color:var(--ink);text-decoration:none;border-bottom:3px solid var(--green);padding-bottom:3px}

/* fast way */
.fastway{left:0;top:1098px;width:1200px;height:542px;background:var(--green);border-top-left-radius:170px;border-bottom-right-radius:200px}
.fastway h2{position:absolute;left:640px;top:100px;font-family:"Righteous",sans-serif;font-weight:400;font-size:31px;color:var(--white);line-height:1.3}
.fastway p{position:absolute;left:640px;top:206px;width:458px;font-size:13px;line-height:1.85;color:var(--white);font-weight:600}
.fastway .btn{position:absolute;left:640px;top:390px}

/* focus */
.focus-item{position:absolute;top:1785px;width:300px;text-align:center}
.focus-item .circle{width:186px;height:186px;border-radius:50%;margin:0 auto;background:radial-gradient(circle at 50% 55%,#7fe67f 0 30%,var(--mist) 32%)}
.focus-item h3{font-family:"Quicksand",sans-serif;font-weight:700;font-size:26px;margin-top:24px;letter-spacing:.5px}

/* added value */
.value{left:0;top:2110px;width:1200px;height:1110px;background:var(--mist);border-top-left-radius:190px;border-bottom-right-radius:200px}
.value-photo{position:absolute;width:378px;height:366px;border-radius:16px}
.value-text h3{font-family:"Righteous",sans-serif;font-weight:400;font-size:28px;margin-bottom:16px}
.value-text p{font-size:16.5px;line-height:1.65;margin-bottom:14px;text-align:justify}
.value-text .btn{font-size:15px;padding:6px 20px}

/* clients */
.client{position:absolute;top:3357px;width:180px;height:68px;background:var(--white);border-radius:4px;box-shadow:0 2px 10px rgba(0,0,0,.14);display:flex;align-items:center;justify-content:center;gap:8px;font-weight:700;font-size:15px}
.client i{width:16px;height:16px;background:var(--ink);display:inline-block}

/* feedback */
.feedback-bg{left:0;top:3762px;width:1200px;height:760px;background:var(--mist-2);border-top-left-radius:320px}
.feedback{left:103px;top:3633px;width:992px;height:284px;background:var(--green);border-radius:0 0 0 70px;color:var(--white);text-align:center}
.feedback .quote{position:absolute;left:90px;top:108px;width:812px;font-size:16px;line-height:1.7;font-weight:500}
.feedback .who{position:absolute;left:0;top:202px;width:992px;font-size:16px;line-height:1.7}
.avatar{left:543px;top:3593px;width:114px;height:114px;border-radius:50%;background:linear-gradient(160deg,#d9dcdc,#9aa0a0);border:3px solid var(--white)}

/* team */
.member{position:absolute;top:4053px;width:300px;text-align:center}
.member .frame{width:226px;height:228px;margin:0 auto;border:12px solid var(--green);border-radius:44px;background:linear-gradient(180deg,#f1f1f1,#6d6f72)}
.member h4{font-family:"Quicksand",sans-serif;font-weight:700;font-size:22px;margin-top:30px}
.member p{font-size:15px;margin-top:6px;font-weight:500}

/* footer */
.footer{left:0;top:4482px;width:1200px;height:380px;background:var(--black);border-top-left-radius:150px;color:var(--white)}
.footer h5{font-family:"Righteous",sans-serif;font-weight:400;font-size:18px;margin-bottom:14px}
.footer ul{list-style:none;font-size:13.5px;line-height:2.25;font-weight:500}
.field{position:absolute;background:var(--white);color:#888;font-size:10px;padding:6px 8px;border-radius:2px}
.footer .bottom-line{position:absolute;left:105px;top:305px;width:990px;height:1px;background:#333}
</style>
</head>
<body>

<!-- header -->
<div class="abs logo" style="left:100px;top:28px;font-size:56px">KAVRIN</div>
<div class="abs topbar">
  <span><i class="ico"><svg width="14" height="14" viewBox="0 0 24 24"><path fill="#fff" d="M6.6 10.8a15 15 0 006.6 6.6l2.2-2.2c.3-.3.7-.4 1-.2 1.1.4 2.3.6 3.6.6.6 0 1 .4 1 1V20c0 .6-.4 1-1 1A17 17 0 013 4c0-.6.4-1 1-1h3.5c.6 0 1 .4 1 1 0 1.3.2 2.5.6 3.6.1.3 0 .7-.2 1z"/></svg></i>+41 44 000 12 34</span>
  <span><i class="ico"><svg width="14" height="14" viewBox="0 0 24 24"><path fill="#fff" d="M3 5h18v14H3zM4 6l8 6 8-6" stroke="#45e14a" stroke-width="1.5"/></svg></i>info@kavrin.ch</span>
  <span style="margin-left:36px;gap:6px"><svg width="18" height="18" viewBox="0 0 24 24" fill="none" stroke="#333" stroke-width="1.6"><circle cx="12" cy="12" r="9"/><path d="M3 12h18M12 3c3 3 3 15 0 18M12 3c-3 3-3 15 0 18"/></svg>⌄ Eng</span>
</div>
<div class="abs nav-line"></div>
<nav class="abs nav"><span>Home</span><span>Commerce</span><span>Online Marketing</span><span>Integration</span><span>Copmany ⌄</span><span>More ⌄</span></nav>
<div class="abs contact-btn">Contact Us</div>

<!-- hero -->
<section class="abs hero">
  <h1>Your Online Marketing Agency In Zurich For SMEs</h1>
  <p>You want to reach the right people online and generate more sales. Contact us!</p>
  <div class="actions"><span class="btn btn-fill">Offers</span><span class="btn btn-line">Deadline</span></div>
  <div class="abs placeholder" role="img" aria-label="Illustration of an online marketing dashboard with megaphone, charts and social icons" style="left:650px;top:75px;width:440px;height:380px;background:radial-gradient(ellipse at 50% 55%,#5ee85f,#8ef18b 60%,var(--green-soft) 80%)"></div>
</section>

<!-- what we do -->
<h2 class="section-title" style="top:700px">What We Do</h2>
<article class="card" style="left:102px">
  <div class="badge" style="background:var(--green-soft)"><svg width="40" height="40" viewBox="0 0 40 40"><rect x="4" y="8" width="32" height="26" rx="3" fill="#111"/><rect x="9" y="16" width="22" height="12" fill="#fff"/><rect x="13" y="19" width="6" height="9" fill="#111"/></svg></div>
  <h3>Your Successful Entry Into e-Commerce</h3>
  <p>Do you want to sell your products or services online? But as an SME, don't you have a marketing department with e-commerce know-how? Then you will face a series of questions that are critical to the</p>
  <a>Read More</a>
</article>
<article class="card" style="left:613px">
  <div class="badge" style="background:var(--orange)"><svg width="40" height="40" viewBox="0 0 40 40"><rect x="6" y="9" width="28" height="22" rx="2" fill="none" stroke="#fff" stroke-width="2.5"/><path d="M13 24l6-6 4 4 5-5" fill="none" stroke="#fff" stroke-width="2.5"/></svg></div>
  <h3>Our Individual Online Marketing Solutions</h3>
  <p>In us you will find a dedicated team with passion, expertise and curiosity for all topics related to e-commerce and online marketing. Our agency gets you online with your products quickly, purposefully</p>
  <a>Read More</a>
</article>

<!-- fast way -->
<section class="abs fastway">
  <div class="abs placeholder" role="img" aria-label="Isometric illustration of a laptop with megaphone and people promoting an online shop" style="left:150px;top:80px;width:400px;height:390px;background:radial-gradient(ellipse at 50% 55%,#ffffff 0 25%,#c9f5c9 45%,var(--green) 72%)"></div>
  <h2>The Fast Way To The<br>Online Shop</h2>
  <p>Our goal is to give you added value with strategic online marketing – a technological competitive advantage that makes the difference. We build on automated processes for setting up and operating your online shop. In this way, we shorten project times, bring web shops online faster and simplify operations. This is how you get to your new web branch quickly and easily. You sell – we ensure the best conditions online.</p>
  <span class="btn btn-ghost">Read More</span>
</section>

<!-- focus -->
<h2 class="section-title" style="top:1692px">Our Focus</h2>
<div class="focus-item" style="left:83px"><div class="circle" role="img" aria-label="eCommerce illustration with shopping cart on a screen"></div><h3>eCommerce</h3></div>
<div class="focus-item" style="left:455px"><div class="circle" role="img" aria-label="Online marketing illustration with megaphone and message icons"></div><h3>Online Marketing</h3></div>
<div class="focus-item" style="left:825px"><div class="circle" role="img" aria-label="Integration illustration with people joining puzzle pieces"></div><h3>Integration</h3></div>

<!-- added value -->
<section class="abs value">
  <h2 class="section-title" style="top:74px">Your Added Value</h2>
  <div class="value-photo" role="img" aria-label="Photo of a consultant drawing a diagram on a whiteboard" style="left:120px;top:195px;background:linear-gradient(135deg,#dfe6ea,#b8c3c9 55%,#8c969c)"></div>
  <div class="abs value-text" style="left:575px;top:278px;width:465px">
    <h3>Automates More Customers</h3>
    <p>We help companies to sell products and services in their own online shop within 3 weeks. The result is more customers.</p>
    <span class="btn btn-fill">More On This</span>
  </div>
  <div class="abs value-text" style="left:120px;top:668px;width:465px">
    <h3>Systematically More Sales</h3>
    <p>Do you have a shop, but no one shops there? Then use modern online marketing to be successful in a few months. We help you with that.</p>
    <span class="btn btn-fill">More On This</span>
  </div>
  <div class="value-photo" role="img" aria-label="Photo of a laptop lid branded with the agency name on a desk" style="left:662px;top:587px;background:linear-gradient(160deg,#1d2f38,#2f5a6a 45%,#0d1418)"></div>
</section>

<!-- clients -->
<h2 class="section-title" style="top:3278px">Our Clients</h2>
<div class="client" style="left:103px"><i></i>Norvale Commerce</div>
<div class="client" style="left:300px">Pendry Shop</div>
<div class="client" style="left:508px"><i style="border-radius:50%"></i>Castello Partners</div>
<div class="client" style="left:715px">Lumio Ads</div>
<div class="client" style="left:913px"><i style="border-radius:50%;background:#777"></i>Brightway Partner</div>

<!-- feedback -->
<div class="abs feedback-bg"></div>
<h2 class="section-title" style="top:3498px">Customer Feedback</h2>
<div class="abs feedback">
  <p class="quote">Many thanks for the really successful vela.de. It fully meets my expectations. The cooperation was professional and uncomplicated. Again any time. Have already received several positive feedbacks for the site.</p>
  <p class="who"><b>Ines Hartmann – Owner of VELA</b><br>occupational therapy and speech therapy</p>
</div>
<div class="abs avatar" role="img" aria-label="Portrait photo of the client"></div>

<!-- team -->
<h2 class="section-title" style="top:3973px">Our Team</h2>
<div class="member" style="left:88px"><div class="frame" role="img" aria-label="Portrait photo of Lukas Brenner"></div><h4>Lukas Brenner</h4><p>eCommerce Manager</p></div>
<div class="member" style="left:446px"><div class="frame" role="img" aria-label="Portrait photo of Martin Seidel"></div><h4>Martin Seidel</h4><p>Online Marketing Manager</p></div>
<div class="member" style="left:803px"><div class="frame" role="img" aria-label="Portrait photo of Sabine Kohler Amrani"></div><h4>Sabine Kohler Amrani</h4><p>Marketing</p></div>

<!-- footer -->
<footer class="abs footer">
  <div class="abs logo" style="left:66px;top:68px;font-size:82px">KAVRIN</div>
  <div class="abs" style="left:420px;top:48px"><h5>Quick Links</h5><ul><li>Home</li><li>Commerce</li><li>Online Marketing</li><li>Integration</li><li>Copmany</li></ul></div>
  <div class="abs" style="left:595px;top:48px"><h5>Other Link</h5><ul><li>Blog</li><li>Contact</li><li>History</li><li>Customer references</li></ul></div>
  <div class="abs" style="left:815px;top:48px"><h5>Get In Touch</h5></div>
  <div class="field" style="left:815px;top:88px;width:132px">Name :</div>
  <div class="field" style="left:955px;top:88px;width:132px">Phone :</div>
  <div class="field" style="left:815px;top:130px;width:272px">Email :</div>
  <div class="field" style="left:815px;top:170px;width:272px;height:66px">Message :</div>
  <div class="abs" style="left:1012px;top:255px;background:var(--green);color:#fff;font-size:12px;font-weight:700;padding:6px 16px;border-radius:14px">Submit</div>
  <div class="bottom-line"></div>
  <div class="abs" style="left:0;top:322px;width:1200px;text-align:center;font-size:12px">Copyright © 2023 kavrin &nbsp;|&nbsp; Privacy policy</div>
  <div class="abs" style="left:1078px;top:324px;font-size:10px">C49</div>
</footer>

</body>
</html>
```